A private security company called "Tavron Security Services Ltd"

Hello everybody,

We need a web page for a company based in NZ. It is mainly an informative website so it would be wonderful if the designer puts their absolute best into making it a website that I would really appreciate. The website needs to show professionalism and also needs to make our web surfers find the information they need in a click. the company's colour is black and silver, and if those two colours could be integrated into the website it would be absolutely lovely. Please do contact me for any information.

Sincerely,
Dorian Vaskel

Industry/Entity Type

Security

```html
<!DOCTYPE html>
<html lang="en">
<head>
<meta charset="utf-8">
<title>Tavron Security Services Ltd</title>
<link href="https://fonts.googleapis.com/css2?family=Open+Sans:wght@300;400;600;700&display=swap" rel="stylesheet">
<style>
:root{
  --black:#0d0d0d;
  --header-top:#2a2a2a;
  --footer:#1a1a1a;
  --white:#ffffff;
  --ink:#1b1b1b;
  --muted:#8c8c8c;
  --silver-light:#e6e9ed;
  --silver-mid:#b9c1cb;
  --band:#f3f3f3;
  --btn-top:#f4f4f4;
  --btn-bottom:#cfcfcf;
}
*{margin:0;padding:0;box-sizing:border-box}
html,body{width:829px;height:1200px;overflow:hidden;background:var(--white)}
body{font-family:'Open Sans',Arial,sans-serif;color:var(--ink);position:relative}
.abs{position:absolute}

/* header */
.site-header{left:0;top:0;width:829px;height:104px;background:linear-gradient(var(--header-top),var(--black))}
.brand{left:76px;top:34px;color:var(--white);font-weight:600;font-size:13px;line-height:16px;letter-spacing:.5px}
.brand span{display:block;font-size:20px;letter-spacing:2px;line-height:24px}
.phone{right:76px;top:20px;color:var(--white);font-size:21px;font-weight:300}
.phone b{font-weight:600}
.main-nav{right:76px;top:66px;display:flex;gap:4px}
.main-nav a{color:var(--white);font-size:10px;text-decoration:none;height:22px;line-height:22px;padding:0 10px}
.main-nav a.active{background:linear-gradient(var(--white),#e2e2e2);color:var(--ink);font-weight:600;border-radius:1px;padding:0 12px}

/* hero */
.hero{left:0;top:104px;width:829px;height:322px;background:linear-gradient(100deg,#e9ecef 0%,#cdd3da 55%,#aeb7c2 100%);overflow:hidden}
.hero-title{left:70px;top:62px;font-size:38px;font-weight:300;letter-spacing:-1.5px;color:var(--ink)}
.hero-title b{font-weight:700}
.hero-text{left:76px;top:120px;width:380px;font-size:11.4px;line-height:15px;color:#2c2c2c;font-weight:300}
.btn-light{left:76px;top:222px;width:92px;height:28px;background:linear-gradient(var(--btn-top),var(--btn-bottom));font-size:10px;font-weight:600;text-align:center;line-height:28px;box-shadow:0 1px 2px rgba(0,0,0,.25)}
.hero-photo{left:510px;top:36px;width:245px;height:220px;border-radius:40% 30% 30% 40%;background:radial-gradient(ellipse at 55% 45%,#e8e3d8 0%,#bdb7aa 45%,rgba(174,183,194,0) 72%)}
.hero-curve{left:0;top:400px}
.slider-dots{left:401px;top:412px;display:flex;gap:3px}
.slider-dots i{width:7px;height:7px;border-radius:50%;background:var(--ink)}

/* services */
.section-title{font-size:20px;font-weight:600;color:var(--black)}
.services-title{left:0;width:829px;top:447px;text-align:center}
.divider{left:76px;top:488px;width:677px;height:6px;background:radial-gradient(ellipse at 50% 0,rgba(0,0,0,.08),rgba(0,0,0,0) 70%)}
.service{top:512px;width:156px}
.service h3{font-size:11.2px;font-weight:600;height:25px}
.service .photo{width:156px;height:106px}
.service p{margin-top:10px;font-size:8.4px;line-height:15px;color:var(--muted);font-weight:300}

/* about */
.about-band{left:0;top:740px;width:829px;height:244px;background:var(--band)}
.about-photo{left:76px;top:767px;width:330px;height:177px;background:linear-gradient(180deg,#4a4f5c 0%,#6e7480 45%,#a58e6a 70%,#7b7f8a 100%)}
.about-title{left:440px;top:760px}
.about-text{left:440px;width:305px;font-size:8.4px;line-height:13.2px;color:var(--muted);font-weight:300}
.btn-dark{left:440px;top:921px;width:78px;height:23px;background:linear-gradient(#3a3a3a,#0e0e0e);color:var(--white);font-size:9.5px;text-align:center;line-height:23px}

/* footer */
.site-footer{left:0;top:984px;width:829px;height:216px;background:var(--footer);color:var(--white)}
.foot-head{font-size:10.4px;font-weight:600;top:30px}
.foot-list{list-style:none;font-size:8.6px;line-height:13.8px;color:#e0e0e0}
.foot-list.spaced{line-height:15.2px}
.testimonial-box{left:380px;top:59px;width:161px;height:66px;background:var(--white);color:#aaa;font-size:8px;line-height:14px;text-align:center;padding:5px 8px;font-weight:300}
.field{background:var(--white);color:#888;font-size:8.2px;padding:3px 6px;left:591px;width:147px}
.btn-send{left:677px;top:139px;width:61px;height:23px;background:linear-gradient(var(--btn-top),var(--btn-bottom));color:var(--ink);font-size:10px;font-weight:600;text-align:center;line-height:23px}
.copyright{left:0;width:829px;top:192px;text-align:center;font-size:8px;color:#ddd}
</style>
</head>
<body>

<header class="site-header abs">
  <div class="brand abs"><span>TAVRON</span>Security Services Ltd.</div>
  <div class="phone abs">Call: <b>123 456 7890</b></div>
  <nav class="main-nav abs">
    <a class="active" href="#">Home</a>
    <a href="#">About Us</a>
    <a href="#">Security Services</a>
    <a href="#">Why Us</a>
    <a href="#">Testimonials</a>
    <a href="#">Contct Us</a>
  </nav>
</header>

<section class="hero abs">
  <h1 class="hero-title abs">WE <b>SECURE</b> YOUR LIFE</h1>
  <p class="hero-text abs">Lorem ipsum dolor sit amet, consectetur adipisicing elit, sed&nbsp; eiusmod tempor incididunt ut labore et dolore magna aliqua ut enim ad minim veniam, quis nostrud exercitation ullamco laborisnisi ut aliquip ex ea commodo consequat. Duis aute irure dolor in reprehenderit in voluptate velit esse cillum dolore eu fugiat nulla pariatur. Excepteur sint occaecat cupidatat non proident, sunt in</p>
  <div class="btn-light abs">Read More</div>
  <div class="hero-photo abs" role="img" aria-label="Photo of a wall-mounted security camera"></div>
</section>
<svg class="hero-curve abs" width="829" height="30" viewBox="0 0 829 30" aria-hidden="true">
  <path d="M0 26 Q414 -6 829 26 L829 30 L0 30 Z" fill="#ffffff"/>
</svg>
<div class="slider-dots abs"><i></i><i></i><i></i></div>

<h2 class="section-title services-title abs">OUR SERVICES</h2>
<div class="divider abs"></div>

<article class="service abs" style="left:76px">
  <h3>GUARD SERVICES</h3>
  <div class="photo" role="img" aria-label="Photo of a guard on the phone in a monitoring room" style="background:linear-gradient(135deg,#8b99ad,#3c4656 60%,#c77a3a)"></div>
  <p>Lorem ipsum dolor consectetur adiicing sed eiusmod tempor incidunt&nbsp; labore dolore magna aliqua ut enim ad minim veniam nostrud exercitation.</p>
</article>
<article class="service abs" style="left:250px">
  <h3>SECURITY CAMERA</h3>
  <div class="photo" role="img" aria-label="Photo of security cameras against the sky" style="background:linear-gradient(180deg,#5f85b8,#a7c0dc)"></div>
  <p>Lorem ipsum dolor consectetur adiicing sed eiusmod tempor incidunt&nbsp; labore dolore magna aliqua ut enim ad minim veniam nostrud exercitation.</p>
</article>
<article class="service abs" style="left:423px">
  <h3>FIXED CAMRA SYSTEMS</h3>
  <div class="photo" role="img" aria-label="Photo of a camera above a city skyline" style="background:linear-gradient(180deg,#3f7fc4,#9cc4e8 65%,#6a7480)"></div>
  <p>Lorem ipsum dolor consectetur adiicing sed eiusmod tempor incidunt&nbsp; labore dolore magna aliqua ut enim ad minim veniam nostrud exercitation.</p>
</article>
<article class="service abs" style="left:597px">
  <h3>ARMED SECURITY OFFICERS</h3>
  <div class="photo" role="img" aria-label="Photo of an officer's duty belt" style="background:linear-gradient(180deg,#7f9fcf,#2c3446 60%,#1e2230)"></div>
  <p>Lorem ipsum dolor consectetur adiicing sed eiusmod tempor incidunt&nbsp; labore dolore magna aliqua ut enim ad minim veniam nostrud exercitation.</p>
</article>

<section class="about-band abs"></section>
<div class="about-photo abs" role="img" aria-label="Photo of operators in a control room with video walls"></div>
<h2 class="section-title about-title abs">ABOUT US</h2>
<p class="about-text abs" style="top:796px">Lorem ipsum dolor sit amet consectetur adipisicing elit sed eiusmod tempor incididunt ut labore et dolore magna aliqua ut enim ad minim veniam quis nostrud exercitation ullamco laboris nisi aliquip ex commodo consequat sunt in culpa qui officia deserunt mollit anim id est laborum</p>
<p class="about-text abs" style="top:862px">Lorem ipsum dolor sit amet, consectetur adipisicing elit, sed do eiusmod tempor incididunt ut labore et dolore magna aliqua. Ut enim ad minim veniam, quis nostrud exercitation ullamco</p>
<div class="btn-dark abs">Read More</div>

<footer class="site-footer abs">
  <h4 class="foot-head abs" style="left:90px">SITE MAP</h4>
  <ul class="foot-list abs" style="left:90px;top:55px">
    <li style="font-weight:600;color:#fff">Home</li><li>About Us</li><li>Security Services</li><li>Why Us</li><li>Testimonials</li><li>Contct Us</li>
  </ul>
  <h4 class="foot-head abs" style="left:217px">LINKS</h4>
  <ul class="foot-list spaced abs" style="left:217px;top:56px">
    <li>Lorem ipsum dolor sit</li><li>Ame cnsectetur adipisicing</li><li>Elit sed&nbsp; eiusmod tempor</li><li>Incididunt ut labore et</li><li>Dolore magna</li>
  </ul>
  <h4 class="foot-head abs" style="left:379px">TESTIMONIALS</h4>
  <div class="testimonial-box abs">Lorem ipsum dolor sit ame cnsecte-tur adipisicing elit&nbsp; eiusmod tempor incididunt ut labore et dolore magna aliqua ut enim ad minim. veniam,</div>
  <h4 class="foot-head abs" style="left:591px;top:28px">QUICK CONTACT</h4>
  <div class="field abs" style="top:59px;height:20px">Email Adderss</div>
  <div class="field abs" style="top:84px;height:45px">Massage</div>
  <div class="btn-send abs">SEND</div>
  <p class="copyright abs">Copy rigthe 2014 ©. Tavron Security Center. All rights reserved</p>
</footer>

</body>
</html>
```